Mobile Friendly Lead Generation Landing Page

We are a web marketing company that specialized in web lead generation. Recently we have started buying media from mobile devices and we need a mobile interface(landing page) where we can collect user data in an effective manner.

Our current mobile landing page is:
http://www.tutorpath.example.com/lp13d/index.aspx?a=true&source=841356
Through this you can see what the steps/questions users need to answer to get matched to a school. We need the design for the whole process.

We are pretty open for design ideas and our goal is to make this mobile optimized landing page have the look and feel of an app...but not an app.
There are several questions in the process but we are open to changing the way they are presented. As in, you can have one question at a time or a few.
The goal is to make this EXTREMELY EASY for users to interact with.

One example that we have liked is:
http://learnvane.example/schools/57214-page1.lvne (please note that this opens only on mobile devices)

Some of these screenshots are attached.

Our web form looks like this:
http://www.tutorpath.example.com/lp88/index.aspx?a=true

```html
<!DOCTYPE html>
<html lang="en">
<head>
<meta charset="utf-8">
<title>Select Area of Interest</title>
<link href="https://fonts.googleapis.com/css2?family=Roboto:wght@300;400&display=swap" rel="stylesheet">
<style>
  :root {
    --yellow: #ffc400;
    --red: #f0201f;
    --green: #1ec51e;
    --panel: #f6f6f6;
    --white: #ffffff;
    --text: #2b2b2b;
    --rule: #c9c9c9;
    --chevron: #8a8a8a;
  }
  * { box-sizing: border-box; margin: 0; padding: 0; }
  html, body {
    width: 678px; height: 1200px; overflow: hidden;
    background: var(--white);
    font-family: "Roboto", "Helvetica Neue", Arial, sans-serif;
  }
  .page { width: 678px; height: 1200px; display: flex; flex-direction: column; }
  .tint-band { height: 42px; flex: none; }
  .tint-band--top { background: linear-gradient(90deg, #f3d4d4 0%, #e6d9c2 40%, #e3e6d3 70%, #e2f2e0 100%); }
  .tint-band--mid { background: linear-gradient(90deg, #ead0d6 0%, #d9cfd3 40%, #d4ddd9 70%, #e2f2e6 100%); }
  .tint-band--bottom { flex: 1; background: linear-gradient(90deg, #d6def3 0%, #e9e6dc 45%, #f2ead4 75%, #fbf0d8 100%); }
  .cta-bar {
    height: 92px; flex: none; background: var(--yellow); color: var(--white);
    display: flex; align-items: center; justify-content: center;
    font-size: 30px; font-weight: 400; letter-spacing: 0.2px;
  }
  .grant-note {
    height: 93px; flex: none; background: var(--panel); color: var(--text);
    display: flex; align-items: center; justify-content: center;
    font-size: 25px; font-weight: 300;
    border-bottom: 1px solid var(--rule);
  }
  .section-title {
    height: 90px; flex: none; background: var(--red); color: var(--white);
    display: flex; align-items: center; justify-content: center;
    font-size: 30px; font-weight: 400;
  }
  .interest-list { list-style: none; background: var(--white); flex: none; border-bottom: 1px solid var(--rule); }
  .interest-item {
    position: relative; height: 92px;
    display: flex; align-items: center; padding-left: 28px;
  }
  .interest-item + .interest-item::before {
    content: ""; position: absolute; top: 0; left: 32px; right: 0;
    border-top: 1px solid var(--rule);
  }
  .interest-icon {
    width: 64px; height: 64px; border-radius: 10px; background: var(--green);
    display: flex; align-items: center; justify-content: center; flex: none;
  }
  .interest-icon svg { width: 44px; height: 44px; }
  .interest-label { margin-left: 19px; font-size: 27px; font-weight: 300; color: var(--text); flex: 1; }
  .interest-chevron { width: 16px; height: 26px; margin-right: 34px; }
</style>
</head>
<body>
<main class="page">
  <div class="tint-band tint-band--top"></div>
  <div class="cta-bar">COMPLETE OUR 3-MINUTE APP</div>
  <div class="grant-note">Get up to $5, 645* per year in Grants if you qualify</div>
  <div class="tint-band tint-band--mid"></div>
  <h1 class="section-title">SELECT AREA OF YOUR INTEREST</h1>
  <ul class="interest-list">
    <li class="interest-item">
      <span class="interest-icon"><svg viewBox="0 0 44 44" fill="none" stroke="#fff" stroke-width="1.6" stroke-linejoin="round"><path d="M34 6 L20 24 L23 27 Z"/><path d="M19 25 C13 25 14 32 9 34 C16 37 23 34 22 28 Z"/></svg></span>
      <span class="interest-label">Art &amp; Design</span>
      <svg class="interest-chevron" viewBox="0 0 16 26" fill="none" stroke="#8a8a8a" stroke-width="3" stroke-linecap="round"><path d="M3 3 L13 13 L3 23"/></svg>
    </li>
    <li class="interest-item">
      <span class="interest-icon"><svg viewBox="0 0 44 44" fill="none" stroke="#fff" stroke-width="1.6"><rect x="6" y="13" width="32" height="22" rx="1"/><path d="M17 13 V9 H27 V13"/><path d="M6 21 H38"/><rect x="20" y="19" width="4" height="4"/></svg></span>
      <span class="interest-label">Business</span>
      <svg class="interest-chevron" viewBox="0 0 16 26" fill="none" stroke="#8a8a8a" stroke-width="3" stroke-linecap="round"><path d="M3 3 L13 13 L3 23"/></svg>
    </li>
    <li class="interest-item">
      <span class="interest-icon"><svg viewBox="0 0 44 44" fill="none" stroke="#fff" stroke-width="1.6" stroke-linejoin="round"><rect x="17" y="6" width="10" height="16" rx="1" transform="rotate(45 22 14)"/><path d="M18 19 L7 30"/><rect x="20" y="34" width="16" height="3"/></svg></span>
      <span class="interest-label">Criminal Justice</span>
      <svg class="interest-chevron" viewBox="0 0 16 26" fill="none" stroke="#8a8a8a" stroke-width="3" stroke-linecap="round"><path d="M3 3 L13 13 L3 23"/></svg>
    </li>
    <li class="interest-item">
      <span class="interest-icon"><svg viewBox="0 0 44 44" fill="#fff" font-family="Roboto, Arial, sans-serif" font-size="13" text-anchor="middle"><text x="22" y="18">ABC</text><rect x="5" y="21" width="34" height="1.4"/><text x="22" y="36">1 2 3</text></svg></span>
      <span class="interest-label">Education &amp; Teaching</span>
      <svg class="interest-chevron" viewBox="0 0 16 26" fill="none" stroke="#8a8a8a" stroke-width="3" stroke-linecap="round"><path d="M3 3 L13 13 L3 23"/></svg>
    </li>
    <li class="interest-item">
      <span class="interest-icon"><svg viewBox="0 0 44 44" fill="none" stroke="#fff" stroke-width="1.6" stroke-linecap="round"><path d="M22 4 V8"/><circle cx="22" cy="11" r="3"/><path d="M20 14 L9 38 M24 14 L35 38"/><path d="M12 28 Q22 34 32 28"/></svg></span>
      <span class="interest-label">Engineering</span>
      <svg class="interest-chevron" viewBox="0 0 16 26" fill="none" stroke="#8a8a8a" stroke-width="3" stroke-linecap="round"><path d="M3 3 L13 13 L3 23"/></svg>
    </li>
    <li class="interest-item">
      <span class="interest-icon"><svg viewBox="0 0 44 44" fill="none" stroke="#fff" stroke-width="1.6" stroke-linejoin="round"><path d="M4 16 L22 8 L40 16"/><path d="M6 16 V36 Q14 32 22 36 Q30 32 38 36 V16"/><path d="M22 14 V36"/><path d="M6 16 Q14 12 22 14 Q30 12 38 16"/></svg></span>
      <span class="interest-label">Other</span>
      <svg class="interest-chevron" viewBox="0 0 16 26" fill="none" stroke="#8a8a8a" stroke-width="3" stroke-linecap="round"><path d="M3 3 L13 13 L3 23"/></svg>
    </li>
  </ul>
  <div class="tint-band tint-band--bottom"></div>
</main>
</body>
</html>
```